Looking for a cool & simple business-card-design for digital agency

Hi!

We are a web agency that offers Reputation Management, Vextor & Seo Services and software development. We like cool things, we like innovative styles.

We have uploaded our logo.

Project Deadline Extended Reason: Client does not want any designs with the colorful logo. Please send us submissions ONLY with the blac and white logo. What the client would like to see:1) Back of the card: is a silver logo on a black background2) front of the card with all the data, please use white background and black logo thank you Added Friday, May 8, 2015

Industry/Entity Type

Software

```html
<!DOCTYPE html>
<html lang="de">
<head>
<meta charset="utf-8">
<title>Kantora AG – Geschäftsausstattung</title>
<link href="https://fonts.googleapis.com/css2?family=Open+Sans:wght@400;600;700&display=swap" rel="stylesheet">
<style>
  :root {
    --backdrop: #d1d1d1;
    --ink: #2a2a2a;
    --ink-soft: #3a3a3a;
    --paper: #f4f4f4;
    --paper-shade: #e9e9e9;
    --silver: #d9d9d9;
    --muted: #8a8a8a;
    --ghost: #dadada;
  }
  * { box-sizing: border-box; margin: 0; padding: 0; }
  html, body { width: 1200px; height: 1000px; overflow: hidden; }
  body {
    background: var(--backdrop);
    font-family: "Open Sans", Arial, sans-serif;
    color: var(--ink);
    position: relative;
  }
  .piece { position: absolute; overflow: hidden; }

  .wordmark { display: flex; align-items: center; gap: 5px; }
  .wordmark__square { width: 8px; height: 8px; background: currentColor; flex: none; }
  .wordmark__name { font-weight: 700; white-space: nowrap; }
  .wordmark__tag {
    font-size: 5px; letter-spacing: 1.6px; font-weight: 400;
    border-top: 1px solid currentColor; padding-top: 1px; margin-top: 1px;
  }

  /* Folder */
  .folder {
    left: 83px; top: 267px; width: 340px; height: 473px;
    background: var(--ink);
  }
  .folder__texture {
    position: absolute; inset: 0;
    background: linear-gradient(160deg, #2f2f2f 0%, #262626 45%, #2d2d2d 70%, #242424 100%);
  }
  .folder__mark {
    position: absolute; left: 0; right: 0; top: 92px;
    text-align: center; color: var(--paper);
    font-weight: 700; font-size: 40px;
  }
  .folder__footer {
    position: absolute; right: 20px; bottom: 26px; color: var(--paper);
  }
  .folder__footer .wordmark__name { font-size: 12px; }

  /* Letterhead */
  .letterhead {
    left: 452px; top: 281px; width: 314px; height: 444px;
    background: var(--paper);
  }
  .letterhead__head { position: absolute; left: 20px; top: 18px; }
  .letterhead__head .wordmark__name { font-size: 9px; }
  .letterhead__ghost {
    position: absolute; right: -6px; bottom: 16px;
    font-weight: 700; font-size: 34px; color: var(--ghost);
  }
  .letterhead__contact {
    position: absolute; left: 186px; bottom: 14px;
    font-size: 3.6px; line-height: 5px; color: var(--muted);
  }

  /* Business cards */
  .card-back {
    left: 811px; top: 253px; width: 126px; height: 84px;
    background: linear-gradient(150deg, #333 0%, #262626 60%, #2e2e2e 100%);
    display: flex; align-items: center; justify-content: center;
    color: var(--silver);
  }
  .card-back .wordmark__name { font-size: 13px; }
  .card-front {
    left: 990px; top: 257px; width: 128px; height: 80px;
    background: var(--paper);
  }
  .card-front__logo { position: absolute; left: 28px; top: 12px; }
  .card-front__logo .wordmark__name { font-size: 7px; }
  .card-front__logo .wordmark__square { width: 6px; height: 6px; }
  .card-front__logo .wordmark__tag { font-size: 3.5px; letter-spacing: 1px; }
  .card-front__person { position: absolute; left: 13px; top: 44px; }
  .card-front__name { font-size: 6px; color: var(--ink-soft); }
  .card-front__role { font-size: 3.6px; font-style: italic; color: var(--muted); }
  .card-front__contact {
    position: absolute; left: 69px; top: 42px;
    font-size: 3.2px; line-height: 4.3px; color: var(--muted);
  }

  /* Envelopes */
  .envelope-front {
    left: 798px; top: 362px; width: 328px; height: 165px;
    background: linear-gradient(180deg, var(--paper) 0%, var(--paper-shade) 100%);
  }
  .envelope-front__head { position: absolute; left: 18px; top: 14px; }
  .envelope-front__head .wordmark__name { font-size: 9px; }
  .envelope-front__ghost {
    position: absolute; right: -4px; bottom: 4px;
    font-weight: 700; font-size: 30px; color: var(--ghost);
  }
  .envelope-front__contact {
    position: absolute; left: 212px; bottom: 6px;
    font-size: 3.4px; line-height: 4.6px; color: var(--muted);
  }
  .envelope-back {
    left: 799px; top: 553px; width: 328px; height: 166px;
    background: var(--paper);
  }
  .envelope-back__flap { position: absolute; left: 0; top: 0; width: 328px; height: 62px; }
  .envelope-back__mark {
    position: absolute; left: 0; right: 0; top: 18px;
    text-align: center; color: var(--paper);
    font-weight: 700; font-size: 13px;
  }
</style>
</head>
<body>

  <section class="piece folder" aria-label="Mappe">
    <div class="folder__texture" role="img" aria-label="Dunkle, facettierte Flächenstruktur"></div>
    <div class="folder__mark">Kantora</div>
    <div class="folder__footer wordmark">
      <span class="wordmark__square"></span>
      <div>
        <div class="wordmark__name">Kantora AG</div>
        <div class="wordmark__tag">DIGITALE STRATEGIEN</div>
      </div>
    </div>
  </section>

  <section class="piece letterhead" aria-label="Briefbogen">
    <div class="letterhead__head wordmark">
      <span class="wordmark__square"></span>
      <div>
        <div class="wordmark__name">Kantora AG</div>
        <div class="wordmark__tag">DIGITALE STRATEGIEN</div>
      </div>
    </div>
    <div class="letterhead__ghost">Kantora</div>
    <address class="letterhead__contact" style="font-style:normal">
      A. Lindenweg 12, 80331 München<br>
      T 089 123 4567 · F 089 123 4568<br>
      E hallo@kantora.de · W www.kantora.de
    </address>
  </section>

  <section class="piece card-back" aria-label="Visitenkarte Rückseite">
    <div class="wordmark__name">Kantora</div>
  </section>

  <section class="piece card-front" aria-label="Visitenkarte Vorderseite">
    <div class="card-front__logo wordmark">
      <span class="wordmark__square"></span>
      <div>
        <div class="wordmark__name">Kantora AG</div>
        <div class="wordmark__tag">DIGITALE STRATEGIEN</div>
      </div>
    </div>
    <div class="card-front__person">
      <div class="card-front__name">Lena Hartmann</div>
      <div class="card-front__role">Managing Director</div>
    </div>
    <address class="card-front__contact" style="font-style:normal">
      A. Lindenweg 12<br>
      80331 München<br>
      T 089 123 4567<br>
      F 089 123 4568<br>
      E hallo@kantora.de<br>
      W www.kantora.de
    </address>
  </section>

  <section class="piece envelope-front" aria-label="Briefumschlag Vorderseite">
    <div class="envelope-front__head wordmark">
      <span class="wordmark__square"></span>
      <div>
        <div class="wordmark__name">Kantora AG</div>
        <div class="wordmark__tag">DIGITALE STRATEGIEN</div>
      </div>
    </div>
    <div class="envelope-front__ghost">Kantora</div>
    <address class="envelope-front__contact" style="font-style:normal">
      A. Lindenweg 12, 80331 München<br>
      T 089 123 4567 · hallo@kantora.de · www.kantora.de
    </address>
  </section>

  <section class="piece envelope-back" aria-label="Briefumschlag Rückseite">
    <svg class="envelope-back__flap" viewBox="0 0 328 62" aria-hidden="true">
      <polygon points="0,0 328,0 328,44 300,58 28,58 0,44" fill="#2a2a2a"/>
    </svg>
    <div class="envelope-back__mark">Kantora</div>
  </section>

</body>
</html>
```